Card design for orthopaedic surgeons working as The Brightwater Joint Centre

Business cards, letterhead

Colors

Designer to choose colors to be used in the design.

Requirements
Must have
• Late addition.
• Cards letterhead must have logos of
• Crestmoor Lindell College of Surgeons
• Varenwood Bone Health Association
Nice to have
• Back of card to have space for appointment time to be added by hand and some blank space for writing incidental other notes.

```html
<!DOCTYPE html>
<html lang="en">
<head>
<meta charset="utf-8">
<title>The Brightwater Joint Centre – Business Cards</title>
<link rel="stylesheet" href="https://fonts.googleapis.com/css2?family=Montserrat:wght@300;400;500;700&display=swap">
<style>
  :root {
    --navy: #06263f;
    --navy-deep: #0a2e4c;
    --sky: #2fa3ec;
    --sky-soft: #5bb8f2;
    --paper: #f3f4f6;
    --paper-shade: #e2e5e9;
    --ink: #0c2f4e;
    --rule: #b9bec5;
    --photo-a: #1d3d9c;
    --photo-b: #3d6fd0;
    --photo-c: #c43a6a;
  }
  * { box-sizing: border-box; margin: 0; padding: 0; }
  html, body { width: 1200px; height: 675px; overflow: hidden; }
  body {
    background: var(--navy);
    font-family: 'Montserrat', sans-serif;
    position: relative;
  }
  .card {
    position: absolute;
    top: 182px;
    width: 540px;
    height: 310px;
    background: linear-gradient(135deg, var(--paper) 0%, var(--paper-shade) 100%);
    overflow: hidden;
    box-shadow: 0 14px 30px rgba(0,0,0,.35);
  }
  .card--front { left: 40px; }
  .card--back { left: 620px; }

  /* Front */
  .front-panel { position: absolute; inset: 0; width: 100%; height: 100%; }
  .front-logo {
    position: absolute;
    left: 58px;
    top: 155px;
    transform: translate(-50%, -50%) rotate(-90deg);
    white-space: nowrap;
    font-weight: 400;
    font-size: 17px;
    letter-spacing: .3px;
    color: var(--sky-soft);
  }
  .badges {
    position: absolute;
    right: 24px;
    top: 22px;
    display: flex;
    gap: 22px;
  }
  .badge { display: flex; flex-direction: column; align-items: center; width: 96px; }
  .badge__mark { width: 52px; height: 52px; background: #9aa6b4; }
  .badge__mark--round { border-radius: 50%; background: #b48b5a; }
  .badge__mark--square { border-radius: 8px; background: #8f6e9c; }
  .badge__caption {
    margin-top: 5px;
    font-size: 6px;
    line-height: 1.3;
    text-align: center;
    text-transform: uppercase;
    color: #55606d;
    letter-spacing: .3px;
  }
  .doctor {
    position: absolute;
    left: 225px;
    top: 115px;
    width: 290px;
  }
  .doctor__name {
    font-size: 24px;
    color: var(--ink);
    font-weight: 300;
    padding-bottom: 4px;
    border-bottom: 1px solid var(--rule);
    display: flex;
    align-items: center;
    justify-content: space-between;
  }
  .doctor__name strong { font-weight: 700; }
  .doctor__title { font-size: 11px; color: var(--ink); margin: 5px 0 10px; }
  .contact-list { list-style: none; }
  .contact {
    display: flex;
    align-items: center;
    justify-content: space-between;
    font-size: 13px;
    color: var(--ink);
    margin-bottom: 8px;
  }
  .icon {
    width: 22px; height: 22px; border-radius: 50%;
    background: var(--navy-deep);
    display: flex; align-items: center; justify-content: center;
    flex-shrink: 0;
  }
  .icon svg { width: 12px; height: 12px; }

  /* Back */
  .back-art { position: absolute; inset: 0; width: 100%; height: 100%; }
  .appointment {
    position: absolute;
    left: 26px;
    top: 26px;
    display: flex;
    width: 240px;
    height: 30px;
  }
  .appointment__label {
    background: var(--sky);
    color: #fff;
    font-weight: 700;
    font-size: 12px;
    padding: 0 14px;
    display: flex; align-items: center;
    white-space: nowrap;
  }
  .appointment__field { flex: 1; background: #fff; border: 1px solid #d6dbe1; }
  .notes { position: absolute; left: 26px; top: 82px; width: 240px; }
  .notes__line { height: 1px; background: var(--rule); margin-bottom: 30px; }
  .back-logo {
    position: absolute;
    right: 26px;
    top: 33px;
    font-size: 15px;
    line-height: 1;
    font-weight: 400;
    color: var(--ink);
    white-space: nowrap;
  }
</style>
</head>
<body>

<section class="card card--front" aria-label="Business card front">
  <svg class="front-panel" viewBox="0 0 540 310" preserveAspectRatio="none">
    <path d="M0 0 H175 C140 80 215 120 175 190 C150 240 170 280 190 310 H0 Z" fill="var(--sky)"/>
    <path d="M0 0 H160 C120 80 195 120 155 190 C130 240 150 280 170 310 H0 Z" fill="var(--navy-deep)"/>
  </svg>
  <div class="front-logo">The Brightwater Joint Centre</div>

  <div class="badges">
    <div class="badge">
      <div class="badge__mark badge__mark--round" role="img" aria-label="Varenwood Bone Health Association fellowship badge"></div>
      <p class="badge__caption">Fellow of the Varenwood Bone Health Association</p>
    </div>
    <div class="badge">
      <div class="badge__mark badge__mark--square" role="img" aria-label="Crestmoor Lindell College of Surgeons badge"></div>
      <p class="badge__caption">Crestmoor Lindell College of Surgeons</p>
    </div>
  </div>

  <div class="doctor">
    <h1 class="doctor__name"><span>Dr. <strong>Lorem Ipsum</strong></span>
      <span class="icon"><svg viewBox="0 0 12 12"><circle cx="6" cy="4" r="2.4" fill="#fff"/><path d="M1.5 11.5 C2 8 10 8 10.5 11.5 Z" fill="#fff"/></svg></span>
    </h1>
    <p class="doctor__title">MS (Ortho), MBBS</p>
    <ul class="contact-list">
      <li class="contact"><span>+61 3 5550 0172</span>
        <span class="icon"><svg viewBox="0 0 12 12"><rect x="3" y="1" width="6" height="10" rx="1" fill="none" stroke="#fff" stroke-width="1.2"/></svg></span></li>
      <li class="contact"><span>hello@brightwaterjoint.example</span>
        <span class="icon"><svg viewBox="0 0 12 12"><rect x="1" y="2.5" width="10" height="7" fill="none" stroke="#fff" stroke-width="1.1"/><path d="M1 2.5 L6 7 L11 2.5" fill="none" stroke="#fff" stroke-width="1.1"/></svg></span></li>
      <li class="contact"><span>118 Harlow Lane, US</span>
        <span class="icon"><svg viewBox="0 0 12 12"><path d="M6 11 C3 7.5 2.5 6 2.5 4.5 A3.5 3.5 0 0 1 9.5 4.5 C9.5 6 9 7.5 6 11 Z" fill="#fff"/><circle cx="6" cy="4.5" r="1.3" fill="var(--navy-deep)"/></svg></span></li>
    </ul>
  </div>
</section>

<section class="card card--back" aria-label="Business card back">
  <svg class="back-art" viewBox="0 0 540 310" preserveAspectRatio="none">
    <defs>
      <linearGradient id="scanTones" x1="0" y1="0" x2="1" y2="0">
        <stop offset="0" stop-color="var(--photo-a)"/>
        <stop offset=".55" stop-color="var(--photo-b)"/>
        <stop offset=".8" stop-color="var(--photo-c)"/>
        <stop offset="1" stop-color="var(--photo-b)"/>
      </linearGradient>
    </defs>
    <rect x="0" y="215" width="540" height="95" fill="url(#scanTones)" role="img" aria-label="Strip of medical imagery showing spine and joint scans"/>
    <path d="M0 205 C150 250 380 240 540 200 V232 C380 262 150 270 0 232 Z" fill="var(--sky)"/>
    <path d="M0 0 H540 V200 C380 240 150 250 0 205 Z" fill="var(--paper)"/>
  </svg>
  <div class="appointment">
    <span class="appointment__label">Appointment time</span>
    <span class="appointment__field"></span>
  </div>
  <div class="notes">
    <div class="notes__line"></div>
    <div class="notes__line"></div>
    <div class="notes__line"></div>
  </div>
  <div class="back-logo">The Brightwater Joint Centre</div>
</section>

</body>
</html>
```